Business card design for my company.
I would like the card's background colour to be black. You can also see our web site to get an idea of our brand. https://www.tmwhomecrafting.com.au/
- Name
- Email

```html
<!DOCTYPE html>
<html lang="en">
<head>
<meta charset="utf-8">
<title>TMW Home Crafting – Business Card</title>
<link rel="stylesheet" href="https://fonts.googleapis.com/css2?family=Roboto:wght@300;400;700;900&display=swap">
<style>
  :root {
    --stage: #232323;
    --card: #2a2a2e;
    --deep: #151517;
    --green: #1f9a48;
    --white: #f4f5f7;
    --muted: #d9dadc;
  }
  * { box-sizing: border-box; margin: 0; padding: 0; }
  html, body { width: 1200px; height: 800px; overflow: hidden; }
  body {
    background: var(--stage);
    font-family: "Roboto", sans-serif;
    position: relative;
  }
  .card {
    position: absolute;
    width: 620px;
    height: 340px;
    background: var(--card);
    border-radius: 26px;
    border-bottom: 6px solid var(--green);
    border-left: 3px solid var(--green);
    box-shadow: 0 14px 28px rgba(0,0,0,.45);
    overflow: hidden;
  }
  .card--back { left: 70px; top: 50px; }
  .card--front { left: 510px; top: 410px; }

  /* back */
  .back-brand {
    position: absolute;
    left: 0; right: 0; top: 110px;
    text-align: center;
    font-weight: 900;
    font-size: 44px;
    letter-spacing: 3px;
    color: var(--deep);
    line-height: 1.1;
  }
  .back-brand span { display: block; font-size: 22px; letter-spacing: 8px; }
  .back-web {
    position: absolute;
    left: 0; right: 0; bottom: 34px;
    text-align: center;
    color: var(--white);
    font-size: 17px;
    font-weight: 400;
  }
  .accent { color: var(--green); }

  /* front */
  .front-brand {
    position: absolute;
    left: 44px; top: 40px;
    display: flex; align-items: center; gap: 12px;
  }
  .front-brand__mark { width: 20px; height: 20px; background: var(--green); }
  .front-brand__name {
    color: var(--white);
    font-weight: 900;
    font-size: 26px;
    letter-spacing: 2px;
    line-height: 1.1;
  }
  .front-deco {
    position: absolute;
    right: 34px; top: 60px;
    text-align: right;
    color: var(--deep);
    font-weight: 900;
    font-size: 64px;
    line-height: 1;
  }
  .person {
    position: absolute;
    left: 44px; top: 128px;
    padding-left: 16px;
    border-left: 7px solid var(--green);
  }
  .person__name { font-size: 34px; line-height: 1.05; }
  .person__first { color: var(--green); font-weight: 900; }
  .person__last { color: var(--white); font-weight: 300; }
  .person__role { color: var(--white); font-size: 15px; margin-top: 2px; }
  .contacts {
    position: absolute;
    left: 66px; top: 212px;
    list-style: none;
  }
  .contacts li {
    display: flex; align-items: center; gap: 12px;
    color: var(--white);
    font-size: 15px;
    line-height: 25px;
  }
  .contacts svg { width: 15px; height: 15px; fill: var(--green); flex: none; }
</style>
</head>
<body>

  <section class="card card--back" aria-label="Card back">
    <div class="back-brand">TMW<span>HOME CRAFTING</span></div>
    <p class="back-web">www.<span class="accent">tmwhomecrafting</span>.com.au</p>
  </section>

  <section class="card card--front" aria-label="Card front">
    <div class="front-brand">
      <span class="front-brand__mark"></span>
      <span class="front-brand__name">TMW HOME CRAFTING</span>
    </div>
    <div class="front-deco" aria-hidden="true">TMW</div>

    <div class="person">
      <p class="person__name"><span class="person__first">Liam</span> <span class="person__last">Hartley</span></p>
      <p class="person__role">General Manager</p>
    </div>

    <ul class="contacts">
      <li>
        <svg viewBox="0 0 24 24"><path d="M6.6 10.8a15.1 15.1 0 0 0 6.6 6.6l2.2-2.2a1 1 0 0 1 1-.25 11.4 11.4 0 0 0 3.6.57 1 1 0 0 1 1 1V20a1 1 0 0 1-1 1A17 17 0 0 1 3 4a1 1 0 0 1 1-1h3.5a1 1 0 0 1 1 1c0 1.25.2 2.45.57 3.57a1 1 0 0 1-.25 1z"/></svg>
        0400 123 456
      </li>
      <li>
        <svg viewBox="0 0 24 24"><path d="M12 2a10 10 0 1 0 0 20 10 10 0 0 0 0-20zm6.9 6h-2.9a15.6 15.6 0 0 0-1.4-3.6A8 8 0 0 1 18.9 8zM12 4c.8 1.2 1.5 2.5 1.9 4h-3.8c.4-1.5 1.1-2.8 1.9-4zM4.3 14a8 8 0 0 1 0-4h3.4a16 16 0 0 0 0 4zm.8 2h2.9c.3 1.3.8 2.5 1.4 3.6A8 8 0 0 1 5.1 16zM8 8H5.1a8 8 0 0 1 4.3-3.6C8.8 5.5 8.3 6.7 8 8zm4 12c-.8-1.2-1.5-2.5-1.9-4h3.8c-.4 1.5-1.1 2.8-1.9 4zm2.3-6H9.7a14.7 14.7 0 0 1 0-4h4.6a14.7 14.7 0 0 1 0 4zm.3 5.6c.6-1.1 1.1-2.3 1.4-3.6h2.9a8 8 0 0 1-4.3 3.6zM16.3 14a16 16 0 0 0 0-4h3.4a8 8 0 0 1 0 4z"/></svg>
        www.<span class="accent">tmwhomecrafting</span>.com.au
      </li>
      <li>
        <svg viewBox="0 0 24 24"><path d="M20 4H4a2 2 0 0 0-2 2v12a2 2 0 0 0 2 2h16a2 2 0 0 0 2-2V6a2 2 0 0 0-2-2zm0 4-8 5-8-5V6l8 5 8-5z"/></svg>
        info@<span class="accent">tmwhomecrafting</span>.com.au
      </li>
      <li>
        <svg viewBox="0 0 24 24"><path d="M12 2a7 7 0 0 0-7 7c0 5.2 7 13 7 13s7-7.8 7-13a7 7 0 0 0-7-7zm0 9.5A2.5 2.5 0 1 1 12 6.5a2.5 2.5 0 0 1 0 5z"/></svg>
        Devonport, Tasmania, Australia
      </li>
    </ul>
  </section>

</body>
</html>
```